refurbishment of diamond cut alloy wheels

we need to design a flyer that will catch the eye of the customer to refurbish diamond cut alloy wheels. we refurbish the wheels by using the latest CNC machine to precision cut and resurface the wheel. we would like before and after pictures of maybe Valtoren, KRT, Pelo wheels to give it a prestige look. The final design should communicate an expensive look and providing a good image for the business. The colours that I would like to use is black and red which should make the flyer stand out. The logo must sit on a black background without the wordings of specialists in GX, Pelo etc and also without servicing, diagnostics etc as well. This flyer is just to communicate refurbishment of alloy wheels to high standard.

Target Market(s)

any members of the public and car dealerships

Industry/Entity Type

Automotive

Colors

Requirements
Must have
• Wow factor with great images of wheels
Nice to have
• Maybe on the front of the flyer it has a picture of a wheel and then on the back of the flyer it has before and after pictures to show how just how incredible it is to refurbish wheels
Should not have
• other makes of wheels apart from KRT, Pelo, and any other high end makes of vehicles wheels

```html
<!DOCTYPE html>
<html lang="en">
<head>
<meta charset="utf-8">
<title>Wheel Refurbishment Flyers</title>
<link href="https://fonts.googleapis.com/css2?family=Montserrat:wght@300;400;600;700;800&display=swap" rel="stylesheet">
<style>
  :root {
    --canvas: #e9e9ea;
    --ink: #2a2a2c;
    --ink-deep: #1b1b1d;
    --red: #b0162a;
    --red-deep: #7e1420;
    --red-soft: #c9545f;
    --white: #ffffff;
    --muted: #b9b9bd;
  }
  * { box-sizing: border-box; margin: 0; padding: 0; }
  html, body { width: 1200px; height: 900px; overflow: hidden; }
  body {
    background: var(--canvas);
    font-family: "Montserrat", sans-serif;
    position: relative;
  }
  .flyer {
    position: absolute;
    top: 125px;
    width: 460px;
    height: 650px;
    overflow: hidden;
    box-shadow: 0 12px 30px rgba(0,0,0,.18);
  }
  .flyer--service { left: 100px; background: var(--ink); }
  .flyer--refurb { left: 640px; background: var(--ink-deep); }
  .flyer__art { position: absolute; inset: 0; width: 460px; height: 650px; }

  /* Service flyer */
  .service__title {
    position: absolute; left: 30px; top: 60px;
    color: var(--white); font-weight: 600; font-size: 34px; line-height: 1.12;
    text-transform: uppercase;
  }
  .service__tagline {
    position: absolute; right: 28px; top: 160px; text-align: right;
    color: var(--white); font-size: 18px; line-height: 1.3;
  }
  .service__tagline strong { font-weight: 600; display: block; }
  .service__tagline span { font-weight: 300; }
  .service__label {
    position: absolute; color: var(--white); font-weight: 700; font-size: 30px;
    line-height: 1; text-transform: uppercase;
  }
  .service__label--before { left: 22px; top: 398px; }
  .service__label--after { left: 300px; top: 404px; }
  .service__copy {
    position: absolute; left: 110px; right: 28px; top: 588px;
    color: var(--muted); font-size: 8.5px; line-height: 1.4; font-style: italic;
  }

  /* Refurb flyer */
  .refurb__brand {
    position: absolute; left: 28px; top: 56px;
    display: flex; align-items: center; gap: 7px;
    color: var(--white); font-size: 12px; font-weight: 600; letter-spacing: .3px;
  }
  .refurb__brand-mark { width: 11px; height: 11px; background: var(--white); }
  .refurb__title {
    position: absolute; left: 28px; top: 88px;
    color: var(--white); text-transform: uppercase; line-height: 1;
  }
  .refurb__title strong { display: block; font-weight: 800; font-size: 34px; }
  .refurb__title span { display: block; font-weight: 300; font-size: 25px; margin-top: 2px; }
  .refurb__tagline {
    position: absolute; left: 28px; top: 158px;
    color: var(--red); font-size: 13px; line-height: 1.3; text-transform: uppercase;
  }
  .refurb__tagline strong { display: block; font-weight: 600; }
  .refurb__tagline span { font-weight: 300; }
  .refurb__copy {
    position: absolute; left: 28px; top: 200px; width: 165px;
    color: var(--muted); font-size: 7.5px; line-height: 1.5;
  }
</style>
</head>
<body>

<section class="flyer flyer--service">
  <svg class="flyer__art" viewBox="0 0 460 650" xmlns="http://www.w3.org/2000/svg">
    <defs>
      <linearGradient id="workshopTint" x1="0" y1="0" x2="1" y2="1">
        <stop offset="0" stop-color="#9a1c28"/>
        <stop offset=".6" stop-color="#7a1620"/>
        <stop offset="1" stop-color="#4c0f15"/>
      </linearGradient>
      <linearGradient id="wheelBefore" x1="0" y1="0" x2="1" y2="1">
        <stop offset="0" stop-color="#d6d6d8"/>
        <stop offset=".5" stop-color="#8d8d91"/>
        <stop offset="1" stop-color="#2c2c30"/>
      </linearGradient>
      <linearGradient id="wheelAfter" x1="0" y1="0" x2="1" y2="1">
        <stop offset="0" stop-color="#eeeeef"/>
        <stop offset=".5" stop-color="#a4a4a8"/>
        <stop offset="1" stop-color="#2c2c30"/>
      </linearGradient>
    </defs>
    <path role="img" aria-label="Photo: technician inspecting the underside of a car beside a tyre, red tinted"
          fill="url(#workshopTint)"
          d="M190 0 H460 V235 C410 250 375 290 350 350 C335 390 320 420 300 440 H0 V305 C70 300 125 250 150 190 C170 140 175 50 190 0 Z"/>
    <path fill="var(--ink)" d="M330 440 C350 400 365 320 460 290 V440 Z"/>
    <rect x="0" y="440" width="460" height="8" fill="var(--ink-deep)"/>
    <polygon role="img" aria-label="Photo: Pelo alloy wheel before refurbishment, dull spokes"
             fill="url(#wheelBefore)" points="0,448 232,448 215,578 0,578"/>
    <polygon role="img" aria-label="Photo: the same wheel after diamond cut refurbishment, bright spokes"
             fill="url(#wheelAfter)" points="240,448 460,448 460,578 223,578"/>
    <rect x="0" y="578" width="460" height="72" fill="var(--ink-deep)"/>
    <rect x="0" y="578" width="460" height="3" fill="var(--red)"/>
  </svg>

  <h1 class="service__title">Best<br>Automotive<br>Service</h1>
  <p class="service__tagline"><strong>LOREM</strong><span>DOLOR SIT AMET</span></p>
  <p class="service__label service__label--before">Before</p>
  <p class="service__label service__label--after">After</p>
  <p class="service__copy">Lorem ipsum is a pseudo-Latin text used in web design, typography, layout. Lorem ipsum is a pseudo-Latin text used in web design, typography, layout. Lorem ipsum is a pseudo-Latin text used in web design, typography, layout. Lorem ipsum is a pseudo-Latin text used in web design, typography, layout.</p>
</section>

<section class="flyer flyer--refurb">
  <svg class="flyer__art" viewBox="0 0 460 650" xmlns="http://www.w3.org/2000/svg">
    <defs>
      <radialGradient id="darkWheel" cx=".3" cy=".35" r=".6">
        <stop offset="0" stop-color="#3a3a3e"/>
        <stop offset="1" stop-color="#1b1b1d"/>
      </radialGradient>
      <linearGradient id="redWheelBg" x1="0" y1="0" x2="1" y2="1">
        <stop offset="0" stop-color="#c46060"/>
        <stop offset=".5" stop-color="#a23a44"/>
        <stop offset="1" stop-color="#6e1a22"/>
      </linearGradient>
      <radialGradient id="heroWheel" cx=".5" cy=".5" r=".55">
        <stop offset="0" stop-color="#d97a84"/>
        <stop offset="1" stop-color="#a8404c"/>
      </radialGradient>
      <linearGradient id="cncBlue" x1="0" y1="0" x2="1" y2="1">
        <stop offset="0" stop-color="#c7d6ec"/>
        <stop offset=".5" stop-color="#4d6fa3"/>
        <stop offset="1" stop-color="#1c2c4a"/>
      </linearGradient>
      <radialGradient id="smallWheel" cx=".5" cy=".5" r=".55">
        <stop offset="0" stop-color="#d45a66"/>
        <stop offset="1" stop-color="#8a1e2a"/>
      </radialGradient>
    </defs>
    <rect role="img" aria-label="Photo: dark close-up of a KRT alloy wheel" x="0" y="0" width="460" height="360" fill="url(#darkWheel)"/>
    <path role="img" aria-label="Photo: large red tinted wheel in a workshop"
          fill="url(#redWheelBg)" d="M0 410 C60 330 150 290 260 280 L460 240 V560 H0 Z"/>
    <rect x="360" y="58" width="120" height="26" rx="13" fill="var(--red)"/>
    <rect x="390" y="72" width="90" height="12" rx="6" fill="var(--red-deep)"/>
    <rect x="150" y="348" width="120" height="26" rx="13" fill="var(--red)"/>
    <rect x="175" y="364" width="70" height="10" rx="5" fill="var(--red-deep)"/>
    <rect x="240" y="520" width="140" height="26" rx="13" fill="var(--red)"/>
    <path fill="var(--ink-deep)" d="M0 560 H460 V650 H0 Z M0 540 L90 540 C120 540 140 560 170 560 H0Z"/>
    <path role="img" aria-label="Photo: stacked red alloy wheels and tyres" fill="var(--red)"
          d="M230 650 C250 600 280 575 330 575 H460 V650 Z"/>
    <polygon fill="var(--ink-deep)" points="465,250 407,350 291,350 233,250 291,150 407,150"/>
    <polygon role="img" aria-label="Photo: red tinted Pelo five spoke alloy wheel" fill="url(#heroWheel)"
             points="445,250 397,333 301,333 253,250 301,167 397,167"/>
    <polygon fill="var(--ink-deep)" points="195,465 160,525 90,525 55,465 90,405 160,405"/>
    <polygon role="img" aria-label="Photo: CNC lathe cutting a wheel surface" fill="url(#cncBlue)"
             points="181,465 153,513 97,513 69,465 97,417 153,417"/>
    <polygon fill="var(--ink-deep)" points="300,505 270,557 210,557 180,505 210,453 270,453"/>
    <polygon role="img" aria-label="Photo: refurbished red multi spoke wheel" fill="url(#smallWheel)"
             points="288,505 264,546 216,546 192,505 216,464 264,464"/>
  </svg>

  <div class="refurb__brand"><span class="refurb__brand-mark"></span>COMPANY NAME</div>
  <h1 class="refurb__title"><strong>Refurbish the</strong><span>Wheels</span></h1>
  <p class="refurb__tagline"><strong>LOREM</strong><span>DOLOR SIT AMET</span></p>
  <p class="refurb__copy">Pellentesque vehicula placerat finibus. Etiam. Lorem ipsum dolor sit amet, consectetur adipiscing elit.</p>
</section>

</body>
</html>
```